Need a website where people can find information about the newly formed Northmere Valuation Oversight Board. Soon after, we will need a place to publish our findings as we audit each municipality in the State of Wisconsin. I have a logo (designed by Artwell Hub), a MS Word document showing the content and a set of images to choose from that we can purchase from Pixmarla.com (found here https://www.pixmarla.com/collaboration/boards/-Xq7TbLwRmNoPzYkAuH-Jd)

```html
<!DOCTYPE html>
<html lang="en">
<head>
<meta charset="utf-8">
<title>Northmere Valuation Oversight Board</title>
<link href="https://fonts.googleapis.com/css2?family=Roboto:wght@400;500;700&family=Lato:wght@400;700&display=swap" rel="stylesheet">
<style>
:root{
  --green:#3d8a1c;
  --green-dark:#2f6e12;
  --ink:#222;
  --text:#333;
  --muted:#555;
  --white:#fff;
  --line:#ddd;
}
*{box-sizing:border-box;margin:0;padding:0}
html,body{width:1200px;height:4141px;overflow:hidden}
body{position:relative;background:var(--white);font-family:"Lato",sans-serif;color:var(--text)}
.abs{position:absolute}
h1,h2,h3,h4{font-family:"Roboto",sans-serif}
.btn{position:absolute;display:flex;align-items:center;justify-content:center;border-radius:24px;font-family:"Roboto",sans-serif;font-weight:500;font-size:16px;text-transform:uppercase;letter-spacing:.3px}
.btn-solid{background:var(--green);color:var(--white)}
.btn-line{border:2px solid var(--green);color:var(--green);background:var(--white)}
.btn-ghost{border:2px solid var(--white);color:var(--white)}
.rule{position:absolute;height:3px;width:36px;background:var(--green)}

/* header */
.header{top:0;left:0;width:1200px;height:92px;background:var(--white)}
.brand{position:absolute;display:flex;align-items:center;gap:8px;font-family:"Roboto",sans-serif;font-weight:700;color:var(--green)}
.brand .dot{border-radius:50%;background:var(--green)}
.call-icon{left:491px;top:23px;width:42px;height:42px;border-radius:50%;background:var(--green);display:flex;align-items:center;justify-content:center}
.call-text{left:548px;top:24px;font-size:11px;color:var(--muted)}
.call-num{left:548px;top:39px;font-family:"Roboto",sans-serif;font-weight:500;font-size:20px;color:var(--ink)}
.social{position:absolute;width:30px;height:30px;border-radius:50%;border:2px solid var(--green)}
.nav{top:92px;left:0;width:1200px;height:49px;background:var(--green);display:flex;align-items:center;justify-content:space-between;padding:0 38px;color:var(--white);font-family:"Roboto",sans-serif;font-weight:500;font-size:11.5px}

/* hero */
.hero{top:141px;left:0;width:1200px;height:601px;background:linear-gradient(180deg,#1d3f86 0%,#3d66ad 35%,#8c98a6 62%,#7a7160 80%,#3f4a2c 100%)}
.hero-title{top:312px;left:0;width:1200px;text-align:center;color:var(--white);font-weight:700;font-size:76px;line-height:76px;text-shadow:0 2px 6px rgba(0,0,0,.4)}
.dots{top:697px;left:574px;display:flex;gap:4px}
.dots span{width:10px;height:10px;border-radius:50%;border:1.5px solid var(--white)}
.dots span.on{background:var(--white)}

/* who we are */
.sec-title{font-weight:500;color:var(--ink);font-size:33px}
.body-copy{font-size:12.5px;line-height:24px;color:var(--text);text-align:justify}
.feature-photo{left:690px;top:784px;width:381px;height:404px;background:linear-gradient(160deg,#d9d2c2,#a8987a 55%,#7c6f57)}
.vertical{left:1110px;top:803px;width:70px;height:385px;writing-mode:vertical-rl;font-family:"Roboto",sans-serif;font-weight:700;font-size:52px;color:#e9e9e9;letter-spacing:2px}

/* uniform */
.farm{top:1274px;left:0;width:1200px;height:549px;background:linear-gradient(180deg,#4b5157 0%,#7a7d80 35%,#5f7a3b 50%,#8b5a22 70%,#a8762f 100%)}
.uni-box{top:1341px;left:580px;width:509px;height:410px;background:rgba(61,138,28,.88);padding:40px 42px;color:var(--white)}
.uni-box h2{font-weight:500;font-size:33px;line-height:38px}
.uni-box .rule{background:var(--white);position:static;margin:12px 0 16px}
.uni-box p{font-size:12.5px;line-height:24px;text-align:justify}

/* audit */
.audit-p{top:1978px;left:222px;width:756px;text-align:center;font-size:12.5px;line-height:24px}
.city{top:2208px;left:0;width:1200px;height:281px;background:linear-gradient(180deg,#bcd6ea 0%,#dfe9ef 45%,#8fa4b5 60%,#5c6f52 85%,#3e5630 100%)}

/* cards */
.card{position:absolute;background:var(--white);border-radius:10px;box-shadow:0 2px 12px rgba(0,0,0,.15);padding:12px}
.card-in{border:1.5px dashed var(--green);border-radius:6px;width:100%;height:100%;position:relative;text-align:center}
.card h3{position:absolute;left:110px;text-align:left;font-weight:500;font-size:16px;line-height:28px;color:var(--ink);text-transform:uppercase}
.card .ico{position:absolute;left:16px;width:76px;height:76px;border-radius:50%;background:var(--green);display:flex;align-items:center;justify-content:center}
.card p{position:absolute;left:20px;right:20px;font-size:11.5px;line-height:24px;color:var(--text)}
.card.featured{background:var(--green)}
.card.featured .card-in{border-color:rgba(255,255,255,.7)}
.card.featured h3,.card.featured p{color:var(--white)}
.card.featured .ico{background:var(--white)}

/* contact */
.contact{top:3132px;left:0;width:1200px;height:615px;background:linear-gradient(135deg,#3c8a1f,#2f7616 50%,#4a9326)}
.field{position:absolute;background:var(--white);font-size:12px;color:#666;padding:15px 14px}

/* footer */
.f-head{font-family:"Roboto",sans-serif;font-weight:700;font-size:14px;color:var(--ink)}
.f-list{list-style:none;font-size:12px;line-height:28px;color:var(--text)}
.f-list li{padding-left:18px;position:relative}
.f-list li::before{content:"»";position:absolute;left:0;top:0;font-size:14px}
.f-line{top:4017px;left:114px;width:978px;height:1px;background:#444}
.f-copy{top:4036px;left:0;width:1200px;text-align:center;font-size:12px;color:var(--ink)}
.f-soc{position:absolute;top:4071px;width:28px;height:28px;border-radius:50%;background:var(--green)}
</style>
</head>
<body>

<header class="header abs">
  <div class="brand" style="left:166px;top:26px;font-size:26px"><span class="dot" style="width:30px;height:30px"></span>NVOB</div>
  <div class="call-icon abs"><svg width="18" height="18" viewBox="0 0 24 24"><path fill="#fff" d="M6.6 10.8a15 15 0 0 0 6.6 6.6l2.2-2.2c.3-.3.7-.4 1-.2 1.1.4 2.3.6 3.6.6.6 0 1 .4 1 1V20c0 .6-.4 1-1 1C10.6 21 3 13.4 3 4c0-.6.4-1 1-1h3.5c.6 0 1 .4 1 1 0 1.3.2 2.5.6 3.6.1.3 0 .7-.2 1z"/></svg></div>
  <div class="call-text abs">Call Us Today</div>
  <div class="call-num abs">+1 888 888 8888</div>
  <span class="social" style="left:740px;top:28px" aria-label="Social link"></span>
  <span class="social" style="left:780px;top:28px" aria-label="Social link"></span>
  <span class="social" style="left:820px;top:28px" aria-label="Social link"></span>
  <span class="social" style="left:860px;top:28px" aria-label="Social link"></span>
  <div class="btn btn-solid" style="left:921px;top:19px;width:146px;height:48px">Donate</div>
</header>

<nav class="nav abs">
  <span>Who We Are</span>
  <span>Wisconsin's Non-Uniform Property Tax Problem</span>
  <span>What is Uniform Taxation?</span>
  <span>Blog</span>
  <span>Audits ▾</span>
  <span>NVOB Recommendations ▾</span>
  <span>Meet the Volunteers ▾</span>
  <span>Corrections</span>
  <span>Contact Us</span>
</nav>

<section>
  <div class="hero abs" role="img" aria-label="State capitol building with a domed rotunda under a blue sky"></div>
  <h1 class="hero-title abs">Northmere Valuation<br>Oversight Board</h1>
  <div class="btn btn-solid" style="left:527px;top:514px;width:146px;height:46px;font-size:15px">Corrections</div>
  <div class="dots abs"><span class="on"></span><span></span><span></span><span></span></div>
</section>

<section>
  <h2 class="sec-title abs" style="left:128px;top:810px">WHO WE ARE</h2>
  <div class="rule" style="left:128px;top:858px"></div>
  <div class="body-copy abs" style="left:128px;top:880px;width:469px">
    <p>The Northmere Valuation Oversight Board (NVOB) is a non-partisan, not-for-profit, watchdog organization with a mission to ensure uniform property taxation statewide. It was started in February of 2022 as the Northmere Valuation Oversight Board, LLC and does business as the Northmere Valuation Oversight Board.</p>
    <p>The Northmere Valuation Oversight Board audits local municipal governments who are responsible for producing a uniform property tax assessment roll each year. The audit looks for evidence that property tax assessments are uniform as well as evidence that they are not uniform.</p>
  </div>
  <div class="btn btn-solid" style="left:128px;top:1108px;width:148px;height:45px">Learn More</div>
  <div class="feature-photo abs" role="img" aria-label="Photo of a carved stone monument"></div>
  <div class="vertical abs">WHO WE ARE</div>
</section>

<section>
  <div class="farm abs" role="img" aria-label="Farm with red barn and silos beside a golden wheat field under grey clouds"></div>
  <div class="uni-box abs">
    <h2>WHAT IS UNIFORM<br>TAXATION?</h2>
    <div class="rule"></div>
    <p>Uniform taxation means similar properties have similar values for taxation purposes. For example, if you own a condominium assessed for tax purposes at $200,000 and your neighbor has the same unit but is assessed at $160,000, your values, and therefore your taxes, will be significantly different. You will be paying more of the tax burden than your neighbor, even though the market value of both units is the same. This is non-uniform taxation.Two properties are often not identical; but to the extent that they are the same their assessed values should be the same. To the extent they are different their assessed values should be different.</p>
  </div>
</section>

<section>
  <h2 class="sec-title abs" style="left:0;top:1910px;width:1200px;text-align:center">AUDIT</h2>
  <div class="rule" style="left:582px;top:1955px"></div>
  <p class="audit-p abs">We audit each municipalities' electronic property tax assessment records. Municipalities are required to keep their assessment records in electronic form, but some do not because the Department of Revenue, who made up the requirement, doesn't enforce their own administrative rules. Not understanding what the word "requirement" means is a longstanding problem at the Department of Revenue and one of the many causes of non-uniformity. Problem with uniformity can nearly always be tracked back to problem with assessed values. Most real estate in Wisconsin is supposed to be assessed at 100% of market value. The largest exceptions are agricultural land, land in DNR forest programs and exempt property. Each municipality should be using CAMA software to calculate property values. For those that do, we use reports generated by their CAMA software to prove or disprove that assessed values are uniform. We also look for evidence that property assessed at less than full market value meets the requirements.</p>
  <div class="city abs" role="img" aria-label="City skyline with a winged lakefront museum under a blue sky"></div>
  <div class="btn btn-solid" style="left:527px;top:2190px;width:146px;height:46px">Learn More</div>
</section>

<section>
  <h2 class="sec-title abs" style="left:0;top:2568px;width:1200px;text-align:center">NVOB RECOMMENDATIONS</h2>
  <div class="rule" style="left:582px;top:2614px"></div>

  <div class="card" style="left:132px;top:2719px;width:300px;height:324px">
    <div class="card-in">
      <div class="ico" style="top:26px"><svg width="36" height="36" viewBox="0 0 24 24" fill="none" stroke="#fff" stroke-width="1.6"><path d="M9 3h6l-2 4h-2z"/><path d="M7 10c-2 3-2 9 5 9s7-6 5-9l-2-3H9z"/><path d="M12 11v6M10 13h3a1 1 0 0 1 0 2h-2"/></svg></div>
      <h3 style="top:36px">Department of<br>Revenue</h3>
      <p style="top:118px">1.Hire enough qualified people with real assessment experience to comply with WI Stat 73.03.<br>2.Develop a pass/fail system to measure uniformity.</p>
      <div class="btn btn-line" style="left:62px;top:246px;width:150px;height:48px">Learn More</div>
    </div>
  </div>

  <div class="card featured" style="left:451px;top:2669px;width:301px;height:328px">
    <div class="card-in">
      <div class="ico" style="top:26px"><svg width="36" height="36" viewBox="0 0 24 24" fill="none" stroke="#3d8a1c" stroke-width="1.6"><path d="M6 3h9l3 3v15H6z"/><path d="M9 9h6M9 12h6M9 15h4"/></svg></div>
      <h3 style="top:36px">State<br>Legislators</h3>
      <p style="top:118px">1.Require the DOR to provide evidence each year that property tax rolls statewide are uniform.<br>2.Come up with a better way to hold municipalities accountable for producing</p>
      <div class="btn btn-ghost" style="left:62px;top:248px;width:150px;height:48px;background:transparent">Learn More</div>
    </div>
  </div>

  <div class="card" style="left:769px;top:2719px;width:301px;height:324px">
    <div class="card-in">
      <div class="ico" style="top:26px"><svg width="38" height="38" viewBox="0 0 24 24" fill="none" stroke="#fff" stroke-width="1.5"><path d="M3 10l9-6 9 6"/><path d="M5 10v9h14v-9"/><path d="M8 12v5M12 12v5M16 12v5M3 20h18"/></svg></div>
      <h3 style="top:36px">Local<br>Municipalities</h3>
      <p style="top:130px">1.Make sure property tax rolls are uniform.<br>2.Take this problem seriously.<br>3.Ask for help if they need it</p>
      <div class="btn btn-line" style="left:62px;top:246px;width:150px;height:48px">Learn More</div>
    </div>
  </div>
</section>

<section>
  <div class="contact abs" role="img" aria-label="Aerial view of a tree-lined residential neighbourhood tinted green"></div>
  <h2 class="sec-title abs" style="left:0;top:3214px;width:1200px;text-align:center;color:var(--white)">CONTACT US</h2>
  <div class="rule" style="left:582px;top:3260px;background:var(--white)"></div>
  <div class="field" style="left:191px;top:3292px;width:257px;height:47px">First Name</div>
  <div class="field" style="left:471px;top:3292px;width:257px;height:47px">Last Name</div>
  <div class="field" style="left:752px;top:3292px;width:257px;height:47px">Email Address</div>
  <div class="field" style="left:191px;top:3371px;width:818px;height:47px">Subject</div>
  <div class="field" style="left:191px;top:3450px;width:818px;height:125px">Message</div>
  <div class="btn btn-ghost" style="left:527px;top:3609px;width:146px;height:46px">Submit</div>
</section>

<footer>
  <div class="brand" style="left:100px;top:3882px;font-size:30px"><span class="dot" style="width:36px;height:36px"></span>NVOB</div>

  <div class="f-head abs" style="left:291px;top:3829px">QUICK LINKS</div>
  <ul class="f-list abs" style="left:291px;top:3856px;width:200px">
    <li>Who We Are</li>
    <li>Wisconsin's Non-Uniform<br>Property Tax Problem</li>
    <li>What is Uniform Taxation?</li>
    <li>Blog</li>
  </ul>
  <ul class="f-list abs" style="left:512px;top:3856px;width:200px">
    <li>Audits</li>
    <li>NVOB Recommendations</li>
    <li>Meet the Volunteers</li>
    <li>Corrections</li>
  </ul>

  <div class="f-head abs" style="left:747px;top:3829px">LEGAL</div>
  <ul class="f-list abs" style="left:743px;top:3856px;width:140px">
    <li>Terms of Use</li>
    <li>Privacy Policy</li>
    <li>Contact</li>
    <li>FAQ</li>
  </ul>

  <div class="f-head abs" style="left:901px;top:3829px">CONTACT US</div>
  <div class="abs" style="left:901px;top:3860px;width:230px;font-size:12px;line-height:28px;color:var(--text)">
    <div style="display:flex;gap:10px"><svg width="12" height="16" viewBox="0 0 24 32" style="margin-top:5px;flex:none"><path fill="#222" d="M12 0a12 12 0 0 0-12 12c0 9 12 20 12 20s12-11 12-20A12 12 0 0 0 12 0zm0 17a5 5 0 1 1 0-10 5 5 0 0 1 0 10z"/></svg><span>123 Lorem ipsum dolor sit amet,<br>consectetur adipiscing elit.</span></div>
    <div style="display:flex;gap:10px;margin-top:6px"><svg width="13" height="13" viewBox="0 0 24 24" style="margin-top:7px;flex:none"><path fill="#222" d="M6.6 10.8a15 15 0 0 0 6.6 6.6l2.2-2.2c.3-.3.7-.4 1-.2 1.1.4 2.3.6 3.6.6.6 0 1 .4 1 1V20c0 .6-.4 1-1 1C10.6 21 3 13.4 3 4c0-.6.4-1 1-1h3.5c.6 0 1 .4 1 1 0 1.3.2 2.5.6 3.6.1.3 0 .7-.2 1z"/></svg><span>+1 888 888 8888</span></div>
    <div style="display:flex;gap:10px;margin-top:12px"><svg width="14" height="11" viewBox="0 0 24 18" style="margin-top:9px;flex:none"><path fill="#222" d="M0 0h24v18H0zm2 2v1l10 7 10-7V2z"/></svg><span>desk@nvob-board.org</span></div>
  </div>

  <div class="f-line abs"></div>
  <div class="f-copy abs">© Copyrights 2022 Northmere Valuation Oversight Board | All Rights Reserved</div>
  <span class="f-soc" style="left:519px" aria-label="Social link"></span>
  <span class="f-soc" style="left:563px" aria-label="Social link"></span>
  <span class="f-soc" style="left:607px" aria-label="Social link"></span>
  <span class="f-soc" style="left:651px" aria-label="Social link"></span>
</footer>

</body>
</html>
```